Summit Builders Web Site / Business Cards

Construction Company that specializes in Water and Fire Damage, Residential ReModels, Landscaping and Building ADU (Accessory Dwelling Unit)

Growing and changing families often need additional space, and a remodeling project can often provide that. Adding a new area, or repurposing an existing one can satisfy this requirement.

Other times, homeowners want to update the look in their kitchen or bathroom with more than just a change of cabinetry or vanity doors and drawers. Whatever your needs are, Summit Builders has skilled workers who are bonded and insured, and ready to make your dreams and visions a reality.

Target Market(s)

Home Owners

Industry/Entity Type

Construction Company

Contact Information for Business Card

Center Logo with our information on the corners

Back side to be Logo Only
Contact Info
CSLB License # 2418596
info@summitbuildersca.example
www.summitbuildersca.example

Coding

Coded - Design and coding required

Number of Pages Required

5+ page

Font styles to use
Serif
Sans Serif

Requirements
Must have
• Using our Logo Colors
Home
About Us
Services
Projects / Portfolio
Contact Us
Nice to have
• Colors matching our Logo
Should not have
• Black because it doesnt match our logo

```html
<!DOCTYPE html>
<html lang="en">
<head>
<meta charset="utf-8">
<title>Summit Builders – Website Layouts</title>
<link href="https://fonts.googleapis.com/css2?family=Montserrat:wght@400;600;700&family=Lato:wght@300;400;700&display=swap" rel="stylesheet">
<style>
:root{
  --orange:#ff6a00;
  --orange-soft:#ff8a33;
  --ink:#2f2f2f;
  --charcoal:#333539;
  --muted:#7a7a7a;
  --line:#e4e4e4;
  --panel:#f4f4f4;
  --white:#ffffff;
  --stage:#ececec;
}
*{box-sizing:border-box;margin:0;padding:0}
html,body{width:1200px;height:4857px;overflow:hidden}
body{background:var(--stage);font-family:"Lato",sans-serif;color:var(--ink);position:relative}
.icons{position:absolute;width:0;height:0}
h2,h3,.display{font-family:"Montserrat",sans-serif}
.photo{display:block}

/* ---------- desktop page ---------- */
.desktop{position:absolute;left:72px;top:420px;width:650px;background:var(--white);box-shadow:0 6px 24px rgba(40,40,40,.15)}
.d-header{height:46px;position:relative;padding:0 50px}
.brand{display:flex;align-items:center;gap:5px;font-family:"Montserrat",sans-serif;font-weight:700;color:var(--charcoal);letter-spacing:.5px}
.brand .mark{background:var(--orange)}
.d-header .brand{position:absolute;left:50px;top:12px;font-size:10px}
.d-header .brand .mark{width:10px;height:10px}
.d-contact{position:absolute;right:100px;top:6px;font-size:6px;line-height:8px;display:flex;gap:4px;align-items:flex-start}
.d-contact .ico{width:9px;height:9px;background:var(--orange);display:flex;align-items:center;justify-content:center}
.d-contact svg{width:6px;height:6px;fill:var(--white)}
.d-contact small{display:block;font-size:4.5px;color:var(--muted)}
.quote-btn{position:absolute;right:50px;top:6px;background:var(--orange);color:var(--white);font-size:5px;font-weight:700;padding:3px 9px;font-family:"Montserrat",sans-serif}
.d-nav{position:absolute;right:50px;top:32px;display:flex;gap:14px;font-size:5px;font-family:"Montserrat",sans-serif;color:var(--ink)}
.d-nav .active{color:var(--orange)}
.d-hero{height:276px;position:relative;overflow:hidden}
.kitchen-photo{background:linear-gradient(160deg,#5b5753 0%,#3e3a37 35%,#6d6a66 60%,#9a9692 82%,#c9c6c1 100%)}
.d-hero .photo{position:absolute;inset:0}
.hero-copy{position:absolute;left:0;right:0;text-align:center;color:var(--white)}
.d-hero .hero-copy{top:86px}
.hero-kicker{font-family:"Montserrat",sans-serif;font-weight:400;letter-spacing:.3px}
.hero-title{font-family:"Montserrat",sans-serif;font-weight:700}
.hero-tag{color:var(--orange);font-family:"Montserrat",sans-serif}
.d-hero .hero-kicker{font-size:13px}
.d-hero .hero-title{font-size:31px;line-height:36px}
.d-hero .hero-tag{font-size:14px}
.hero-btns{display:flex;justify-content:center;gap:5px;margin-top:8px}
.hero-btns span{font-size:5px;font-weight:700;font-family:"Montserrat",sans-serif;padding:4px 10px;background:var(--white);color:var(--ink)}
.hero-btns span.primary{background:var(--orange);color:var(--white)}
.slider-dots{height:14px;display:flex;justify-content:flex-end;gap:3px;padding:4px 40px 0 0}
.slider-dots i{width:8px;height:8px;border-radius:50%;background:#ddd}
.sec-title{font-family:"Montserrat",sans-serif;font-weight:600;text-align:center;color:var(--ink)}
.d-who{height:246px;position:relative}
.d-who .sec-title{font-size:17px;padding-top:14px}
.who-copy{position:absolute;left:50px;top:110px;width:240px}
.who-copy .kicker{font-size:8px}
.who-copy h3{font-size:14px;font-weight:600;margin-bottom:5px}
.tiny{font-size:4.6px;line-height:6.5px;color:var(--muted)}
.who-cards{position:absolute;left:325px;top:52px;display:grid;grid-template-columns:132px 132px;gap:8px}
.value-card{height:80px;background:var(--white);box-shadow:0 1px 5px rgba(0,0,0,.12);display:flex;flex-direction:column;align-items:center;justify-content:center;text-align:center;font-size:6px;line-height:8px}
.value-card svg{width:22px;height:22px;margin-bottom:6px;fill:none;stroke:var(--orange);stroke-width:2}
.value-card.featured{background:var(--charcoal);color:var(--white)}
.value-card.featured svg{stroke:var(--white)}
.d-services{height:228px;background:var(--panel);position:relative;overflow:hidden}
.d-services h2{position:absolute;left:50px;top:22px;font-size:18px;font-weight:700}
.d-services .intro{position:absolute;left:50px;top:46px;width:440px}
.service-strip{position:absolute;left:50px;top:80px;display:flex;gap:4px}
.service-item{width:128px}
.service-item .photo{height:82px;clip-path:polygon(22% 0,100% 0,78% 100%,0 100%)}
.fire-photo{background:linear-gradient(180deg,#a7c3de,#8a6a5a 55%,#4d3a33)}
.remodel-photo{background:linear-gradient(180deg,#c7d3d9,#9b8c7b 50%,#6b5a4b)}
.landscape-photo{background:linear-gradient(180deg,#9cc0de,#7a9a6a 55%,#53703f)}
.service-item h4{font-size:7px;font-weight:400;margin:4px 0 2px}
.couple-photo{position:absolute;right:0;top:0;width:170px;height:228px;background:linear-gradient(150deg,#b59a7c,#8b6b4e 45%,#d3c7b7);clip-path:polygon(30% 0,100% 0,100% 100%,0 100%)}
.d-other{height:278px}
.d-other .sec-title{font-size:17px;padding-top:26px}
.other-grid{display:flex;gap:6px;padding:10px 50px 0}
.other-card{width:179px}
.other-card .photo{height:118px}
.kitchen2-photo{background:linear-gradient(180deg,#3f4347,#8f9396 55%,#d8d8d8)}
.bath-photo{background:linear-gradient(180deg,#cdbfac,#eee6da 60%,#b9a48c)}
.doors-photo{background:linear-gradient(180deg,#4e5653,#8e948f 55%,#c6c8c3)}
.other-card h4{font-size:7px;font-weight:700;margin:5px 0 2px}
.read-more{display:inline-block;margin-top:4px;background:var(--orange);color:var(--white);font-size:4.5px;font-weight:700;padding:3px 6px;font-family:"Montserrat",sans-serif}
.d-whatwedo{height:242px;background:var(--panel)}
.d-whatwedo .sec-title{font-size:17px;padding-top:18px}
.wwd-grid{display:grid;grid-template-columns:repeat(3,1fr);row-gap:14px;padding:10px 60px 0}
.wwd-item{text-align:center;font-size:7px;font-family:"Montserrat",sans-serif}
.wwd-ico{width:46px;height:46px;border-radius:50%;background:var(--orange);display:flex;align-items:center;justify-content:center;margin:0 auto 6px;border:3px solid #ffd7bd}
.wwd-ico svg{width:22px;height:22px;fill:var(--white)}
.d-recent{height:278px}
.d-recent .sec-title{font-size:17px;padding-top:28px}
.recent-grid{display:grid;grid-template-columns:136px 136px 274px;grid-template-rows:90px 90px;gap:3px;padding:8px 50px 0}
.recent-grid .big{grid-column:3;grid-row:1/3}
.room1{background:linear-gradient(160deg,#6b4a38,#b08a6b 60%,#3f2c22)}
.room2{background:linear-gradient(160deg,#d9d0c4,#8c6a4c 60%,#4a3426)}
.room3{background:linear-gradient(160deg,#2e4b3a,#58796a 55%,#7fb6d1)}
.room4{background:linear-gradient(160deg,#7d858a,#cfd3d4 50%,#6b6f70)}
.room5{background:linear-gradient(160deg,#c9c7c2,#ffffff 50%,#8e8a84)}
.d-stats{height:68px;background:linear-gradient(90deg,#2c2e31,#3b3d41);display:flex;justify-content:space-around;align-items:center;padding:0 30px}
.stat{text-align:center;color:var(--white)}
.stat b{display:block;color:var(--orange);font-family:"Montserrat",sans-serif;font-weight:700;font-size:10px}
.stat span{font-size:4.6px}
.d-clients{height:253px;position:relative}
.d-clients .sec-title{font-size:17px;padding-top:28px}
.testimonial{position:absolute;background:var(--white);box-shadow:0 1px 6px rgba(0,0,0,.13);padding:12px}
.testimonial .who{display:flex;align-items:center;gap:6px;margin-top:10px}
.avatar{width:24px;height:24px;border-radius:50%;background:linear-gradient(160deg,#cfcfcf,#8d8d8d)}
.who b{display:block;font-size:6px}
.who small{font-size:4px;color:var(--muted)}
.d-footer{height:190px;background:#f7f7f7;position:relative;padding:20px 50px 0}
.foot-cols{display:grid;grid-template-columns:150px 100px 110px 130px 70px;gap:6px}
.foot-cols h5{font-size:7px;font-weight:700;margin-bottom:6px}
.foot-cols li{list-style:none;font-size:4.6px;line-height:8px;color:var(--muted);display:flex;gap:3px;align-items:center}
.dot{width:6px;height:6px;border-radius:50%;background:#666;flex:none}
.foot-brand{position:absolute;left:0;right:0;bottom:22px;display:flex;justify-content:center}
.foot-brand .brand{font-size:9px}
.foot-brand .mark{width:8px;height:8px}
.copyright{position:absolute;left:0;right:0;bottom:10px;text-align:center;font-size:4.6px;color:var(--muted)}
.copyright em{color:var(--orange);font-style:normal}

/* ---------- mobile page ---------- */
.mobile{position:absolute;left:808px;top:420px;width:274px;background:var(--white);box-shadow:0 6px 24px rgba(40,40,40,.15)}
.m-logo{height:76px;display:flex;align-items:center;justify-content:center}
.m-logo .brand{font-size:14px}
.m-logo .mark{width:12px;height:12px}
.m-menu{height:32px;background:var(--orange);display:flex;align-items:center;padding-left:14px}
.m-menu svg{width:20px;height:14px;stroke:var(--white);stroke-width:2}
.m-hero{height:113px;position:relative;overflow:hidden}
.m-hero .photo{position:absolute;inset:0}
.m-hero .hero-copy{top:38px}
.m-hero .hero-kicker{font-size:6px}
.m-hero .hero-title{font-size:13px;line-height:16px}
.m-hero .hero-tag{font-size:6px}
.m-hero .hero-btns{margin-top:3px}
.m-hero .hero-btns span{font-size:3.5px;padding:2px 6px}
.m-who{height:685px;padding:0 7px}
.m-who .sec-title{font-size:19px;padding-top:26px}
.m-who .kicker{font-size:12px;margin-top:16px}
.m-who h3{font-size:18px;font-weight:600;margin-bottom:6px}
.m-who p{font-size:8.5px;line-height:13px;color:var(--muted)}
.m-cards{display:flex;flex-direction:column;align-items:center;gap:10px;margin-top:32px}
.m-cards .value-card{width:184px;height:108px;font-size:10px;line-height:13px}
.m-cards .value-card svg{width:32px;height:32px}
.m-services{height:308px;text-align:center}
.m-services .sec-title{font-size:19px;padding-top:0}
.m-services .photo{width:256px;height:138px;margin:16px auto 0;clip-path:polygon(14% 0,100% 0,86% 100%,0 100%)}
.m-services h4,.m-other h4{font-size:15px;font-weight:400;margin-top:8px}
.m-services p{font-size:9px;line-height:12px;color:var(--muted);padding:0 30px}
.pager{display:flex;justify-content:center;gap:8px;margin-top:18px}
.pager i{width:20px;height:20px;border-radius:50%;border:1px solid var(--line);display:flex;align-items:center;justify-content:center}
.pager svg{width:8px;height:8px;stroke:var(--ink);stroke-width:2;fill:none}
.m-other{height:391px}
.m-other .sec-title{font-size:19px;padding-top:0}
.m-other .photo{width:260px;height:170px;margin:12px auto 0}
.m-other .body{padding:0 7px}
.m-other h4{font-weight:700;font-size:12px}
.m-other p{font-size:8.5px;line-height:12px;color:var(--ink)}
.m-other .read-more{font-size:8px;padding:6px 9px;margin-top:10px}
.m-whatwedo{height:557px;padding-top:12px}
.m-whatwedo .sec-title{font-size:19px}
.m-wwd{display:flex;flex-direction:column;align-items:center;gap:12px;margin-top:18px}
.m-wwd .wwd-item{font-size:9.5px}
.m-wwd .wwd-ico{width:52px;height:52px;margin-bottom:4px}
.m-wwd .wwd-ico svg{width:26px;height:26px}
.m-recent{height:226px;background:var(--panel);position:relative}
.m-recent .sec-title{font-size:19px;padding-top:20px}
.m-recent .photo{position:absolute;left:24px;top:58px;width:226px;height:152px}
.m-recent .arrow{position:absolute;top:128px;width:8px;height:10px;stroke:var(--ink);stroke-width:1.5;fill:none}
.m-stats{height:274px;background:linear-gradient(180deg,#2c2e31,#3a3c40);text-align:center;padding-top:16px}
.m-stats .stat{margin-bottom:12px}
.m-stats .stat b{font-size:24px;line-height:26px}
.m-stats .stat span{font-size:12px;letter-spacing:.2px}
.m-clients{height:217px;background:var(--panel);position:relative}
.m-clients .sec-title{font-size:19px;padding-top:18px}
.m-clients .testimonial{left:18px;top:60px;width:238px;padding:10px}
.m-clients .testimonial .tiny{font-size:6px;line-height:8px}
.m-clients .pager{position:absolute;left:0;right:0;top:176px;margin:0}
.m-footer{height:1142px;background:var(--panel);padding:34px 7px 0;position:relative}
.m-footer h5{font-size:19px;font-weight:400;margin:18px 0 10px}
.m-footer h5:first-child{margin-top:0}
.m-footer p,.m-footer li{font-size:11px;line-height:16px;color:var(--muted);list-style:none}
.m-footer li{margin-bottom:9px;display:flex;gap:6px;align-items:center}
.m-footer hr{border:0;border-top:1px solid #d8d8d8;margin:16px 0}
.m-footer .ci svg{width:12px;height:12px;fill:var(--orange);flex:none}
.m-footer .soc .dot{width:18px;height:18px;background:#3a3a3a}
.m-footer .foot-brand{bottom:58px}
.m-footer .foot-brand .brand{font-size:12px}
.m-footer .copyright{bottom:26px;font-size:9px;line-height:12px;padding:0 30px}
</style>
</head>
<body>

<svg class="icons" aria-hidden="true">
  <defs>
    <symbol id="i-star" viewBox="0 0 24 24"><path d="M12 2.5l2.9 6.2 6.6.7-5 4.5 1.4 6.6L12 17.2l-5.9 3.3 1.4-6.6-5-4.5 6.6-.7z"/></symbol>
    <symbol id="i-hands" viewBox="0 0 24 24"><path d="M2 10l5-3 4 2 4-2 7 3M6 13l3 3 2-1 2 2 2-1 3-3M9 9l3 3"/></symbol>
    <symbol id="i-thumb" viewBox="0 0 24 24"><path d="M3 11h4v10H3zM7 11l4-8c2 0 3 1 2.5 3.5L13 9h6c1.5 0 2.3 1.3 2 2.5l-2 7.5c-.3 1.2-1.2 2-2.4 2H7"/></symbol>
    <symbol id="i-team" viewBox="0 0 24 24"><circle cx="6" cy="7" r="2.5"/><circle cx="18" cy="7" r="2.5"/><circle cx="12" cy="12" r="2.5"/><path d="M2 15c0-2.5 2-4 4-4M22 15c0-2.5-2-4-4-4M7 21c0-3 2.2-5 5-5s5 2 5 5"/></symbol>
    <symbol id="i-house" viewBox="0 0 24 24"><path d="M12 3l9 8h-3v9h-5v-6h-2v6H6v-9H3z"/></symbol>
    <symbol id="i-build" viewBox="0 0 24 24"><path d="M4 21V9l8-5 8 5v12h-6v-6h-4v6zM9 11h2v2H9zm4 0h2v2h-2z"/></symbol>
    <symbol id="i-layout" viewBox="0 0 24 24"><path d="M4 3h16v18H4zm2 2v6h5V5zm7 0v3h5V5zm0 5v9h5v-9zM6 13v6h5v-6z"/></symbol>
    <symbol id="i-brick" viewBox="0 0 24 24"><path d="M3 4h8v4H3zm10 0h8v4h-8zM3 10h4v4H3zm6 0h8v4H9zm10 0h2v4h-2zM3 16h8v4H3zm10 0h8v4h-8z"/></symbol>
    <symbol id="i-reno" viewBox="0 0 24 24"><path d="M3 21V10l7-5 7 5v11zM14 3h5v3h-5zM16 6h1v4h-1zM7 14h6v3H7z"/></symbol>
    <symbol id="i-shield" viewBox="0 0 24 24"><path d="M12 2l8 3v6c0 5-3.5 9-8 11-4.5-2-8-6-8-11V5zm-1 13l6-6-1.4-1.4L11 12.2 8.4 9.6 7 11z"/></symbol>
    <symbol id="i-phone" viewBox="0 0 24 24"><path d="M6.6 10.8a15 15 0 006.6 6.6l2.2-2.2a1 1 0 011-.25 11.4 11.4 0 003.6.6 1 1 0 011 1V20a1 1 0 01-1 1A17 17 0 013 4a1 1 0 011-1h3.5a1 1 0 011 1c0 1.25.2 2.45.6 3.6a1 1 0 01-.25 1z"/></symbol>
    <symbol id="i-pin" viewBox="0 0 24 24"><path d="M12 2a7 7 0 00-7 7c0 5.2 7 13 7 13s7-7.8 7-13a7 7 0 00-7-7zm0 9.5A2.5 2.5 0 1112 6a2.5 2.5 0 010 5.5z"/></symbol>
    <symbol id="i-mail" viewBox="0 0 24 24"><path d="M3 5h18v14H3zm2 2v.5l7 5 7-5V7z"/></symbol>
    <symbol id="i-left" viewBox="0 0 10 10"><path d="M6.5 1.5L3 5l3.5 3.5"/></symbol>
    <symbol id="i-right" viewBox="0 0 10 10"><path d="M3.5 1.5L7 5 3.5 8.5"/></symbol>
  </defs>
</svg>

<!-- ================= Desktop home page ================= -->
<main class="desktop">
  <header class="d-header">
    <div class="brand"><span class="mark"></span>SUMMIT BUILDERS</div>
    <div class="d-contact">
      <span class="ico"><svg><use href="#i-phone"/></svg></span>
      <div>+1 555 014 2287<small>office@summitbuildersca.example</small></div>
    </div>
    <span class="quote-btn">GET A QUOTE</span>
    <nav class="d-nav">
      <span class="active">HOME</span><span>ABOUT US</span><span>SERVICES</span><span>PROJECTS / PORTFOLIO</span><span>CONTACT US</span>
    </nav>
  </header>

  <section class="d-hero">
    <div class="photo kitchen-photo" role="img" aria-label="Remodeled kitchen with dark cabinets and marble island"></div>
    <div class="hero-copy">
      <p class="hero-kicker">THE BEST CHOOSE US</p>
      <h1 class="hero-title">SUMMIT BUILDERS</h1>
      <p class="hero-tag">Because We Deliver</p>
      <div class="hero-btns"><span class="primary">GET STARTED</span><span>CONTACT US</span></div>
    </div>
  </section>
  <div class="slider-dots"><i></i><i></i></div>

  <section class="d-who">
    <h2 class="sec-title">WHO WE ARE</h2>
    <div class="who-copy">
      <p class="kicker">We Deliver</p>
      <h3>Landmark Projects</h3>
      <p class="tiny">We are skilled builders who turn every plan into a lasting home. From the first sketch of a new room to the final walk through, our crew keeps your project on time, on budget and built to last for years.</p>
    </div>
    <div class="who-cards">
      <div class="value-card"><svg><use href="#i-star"/></svg>We've<br>Reputaion For Excellence</div>
      <div class="value-card"><svg><use href="#i-hands"/></svg>We<br>Build Partnerships</div>
      <div class="value-card featured"><svg><use href="#i-thumb"/></svg>Guided<br>By Commitment</div>
      <div class="value-card"><svg><use href="#i-team"/></svg>A Team<br>Of Professionals</div>
    </div>
  </section>

  <section class="d-services">
    <h2>OUR SERVICES</h2>
    <p class="intro tiny">From damage repair to full remodels, our bonded and insured crew handles every stage of the work with care and clear pricing for each home.</p>
    <div class="service-strip">
      <div class="service-item"><div class="photo fire-photo" role="img" aria-label="Home with fire damaged roof"></div><h4>Fire Damage</h4><p class="tiny">If you use this site regularly and would like to help keep the site.</p></div>
      <div class="service-item"><div class="photo remodel-photo" role="img" aria-label="Remodeled residential interior"></div><h4>Residential ReModels</h4><p class="tiny">If you use this site regularly and would like to help keep the site.</p></div>
      <div class="service-item"><div class="photo landscape-photo" role="img" aria-label="Landscaped house with lawn"></div><h4>Landscaping and Building</h4><p class="tiny">If you use this site regularly and would like to help keep the site.</p></div>
    </div>
    <div class="couple-photo" role="img" aria-label="Homeowners reviewing plans in their new kitchen"></div>
  </section>

  <section class="d-other">
    <h2 class="sec-title">OTHER SERVICES</h2>
    <div class="other-grid">
      <div class="other-card"><div class="photo kitchen2-photo" role="img" aria-label="Modern gray kitchen"></div><h4>Kitchen</h4><p class="tiny">Fresh layouts, new counters and cabinets fitted to the way your family cooks.</p><span class="read-more">READ MORE</span></div>
      <div class="other-card"><div class="photo bath-photo" role="img" aria-label="Bright remodeled bathroom"></div><h4>Bathroom</h4><p class="tiny">Tile, vanities and showers rebuilt for comfort with clean lasting finishes.</p><span class="read-more">READ MORE</span></div>
      <div class="other-card"><div class="photo doors-photo" role="img" aria-label="Cabinet doors and drawers"></div><h4>Doors and Drawers</h4><p class="tiny">Custom doors and drawers that refresh a room without a full rebuild.</p><span class="read-more">READ MORE</span></div>
    </div>
  </section>

  <section class="d-whatwedo">
    <h2 class="sec-title">WHAT WE DO</h2>
    <div class="wwd-grid">
      <div class="wwd-item"><div class="wwd-ico"><svg><use href="#i-house"/></svg></div>Home Construction</div>
      <div class="wwd-item"><div class="wwd-ico"><svg><use href="#i-build"/></svg></div>Building Remodeling</div>
      <div class="wwd-item"><div class="wwd-ico"><svg><use href="#i-layout"/></svg></div>Interior Design</div>
      <div class="wwd-item"><div class="wwd-ico"><svg><use href="#i-brick"/></svg></div>Exterior Design</div>
      <div class="wwd-item"><div class="wwd-ico"><svg><use href="#i-reno"/></svg></div>Renovation</div>
      <div class="wwd-item"><div class="wwd-ico"><svg><use href="#i-shield"/></svg></div>Safety Management</div>
    </div>
  </section>

  <section class="d-recent">
    <h2 class="sec-title">RECENT WORK</h2>
    <div class="recent-grid">
      <div class="photo room1" role="img" aria-label="Finished living room"></div>
      <div class="photo room2" role="img" aria-label="New wooden staircase"></div>
      <div class="photo room3" role="img" aria-label="House with backyard pool"></div>
      <div class="photo room4" role="img" aria-label="Open plan interior"></div>
      <div class="photo room5 big" role="img" aria-label="White modern kitchen with island"></div>
    </div>
  </section>

  <section class="d-stats">
    <div class="stat"><b>53</b><span>TOTAL PROJECTS</span></div>
    <div class="stat"><b>371</b><span>STAFF MEMBERS</span></div>
    <div class="stat"><b>15</b><span>WORKING IN STATES</span></div>
    <div class="stat"><b>2,600</b><span>HOURS FOR WORK</span></div>
  </section>

  <section class="d-clients">
    <h2 class="sec-title">OUR CLIENTS</h2>
    <div class="testimonial" style="left:50px;top:64px;width:268px">
      <p class="tiny">"And for all the wonderful work you and your crew are doing. Our team has nothing but good things to say – we are really fortunate to have found you for this project!"</p>
      <div class="who"><span class="avatar" role="img" aria-label="Client portrait"></span><div><b>John Doe</b><small>Chairman</small></div></div>
    </div>
    <div class="testimonial" style="left:332px;top:100px;width:268px">
      <p class="tiny">Summit Builders is one of the best general contractors we have worked with. The entire team carefully delivered a project of exceptional quality within our schedule and budget. We hope to work with them again in the near future.</p>
      <div class="who"><span class="avatar" role="img" aria-label="Client portrait"></span><div><b>Irene Calder</b><small>Project Manager</small></div></div>
    </div>
  </section>

  <footer class="d-footer">
    <div class="foot-cols">
      <div><h5>Company</h5><p class="tiny">We work 7 days a week, every day excluding major holidays. Contact us if you have an emergency, with our hotline and contact form.<br><br>Monday – friday: 10:00 – 16:00<br>Saturday: 12:00 – 15:00<br>Sunday and holidays: 09:00 – 12:00</p></div>
      <div><h5>Quick Links</h5><ul><li>Home</li><li>About Us</li><li>Services</li><li>Projects / Portfolio</li><li>Contact Us</li></ul></div>
      <div><h5>What We Do</h5><ul><li>Home Construction</li><li>Building Remodeling</li><li>Interior Design</li><li>Exterior Design</li><li>Renovation</li><li>Safety Management</li></ul></div>
      <div><h5>Contact Us</h5><ul><li>418 W Harbor Crest Ave Tustin, CA 92780</li><li>+1 555 014 2287</li><li>office@summitbuildersca.example</li></ul></div>
      <div><h5>Follow Us</h5><ul><li><span class="dot"></span>Friendbook</li><li><span class="dot"></span>Chirper</li><li><span class="dot"></span>WorkLink</li><li><span class="dot"></span>ViewTube</li></ul></div>
    </div>
    <div class="foot-brand"><div class="brand"><span class="mark"></span>SUMMIT BUILDERS</div></div>
    <p class="copyright">COPYRIGHT © 2020 <em>SUMMIT BUILDERS</em>. ALL RIGHTS RESERVED.</p>
  </footer>
</main>

<!-- ================= Mobile home page ================= -->
<main class="mobile">
  <header class="m-logo"><div class="brand"><span class="mark"></span>SUMMIT BUILDERS</div></header>
  <div class="m-menu"><svg viewBox="0 0 20 14"><path d="M0 2h20M0 7h20M0 12h20"/></svg></div>
  <section class="m-hero">
    <div class="photo kitchen-photo" role="img" aria-label="Remodeled kitchen with dark cabinets and marble island"></div>
    <div class="hero-copy">
      <p class="hero-kicker">THE BEST CHOOSE US</p>
      <h1 class="hero-title">SUMMIT BUILDERS</h1>
      <p class="hero-tag">Because We Deliver</p>
      <div class="hero-btns"><span class="primary">GET STARTED</span><span>CONTACT US</span></div>
    </div>
  </section>

  <section class="m-who">
    <h2 class="sec-title">WHO WE ARE</h2>
    <p class="kicker">We Deliver</p>
    <h3>Landmark Projects</h3>
    <p>We are skilled builders who turn every plan into a lasting home. From the first sketch of a new room to the final walk through, our crew keeps your project on time and on budget, built with care for the family living in it.</p>
    <div class="m-cards">
      <div class="value-card"><svg><use href="#i-star"/></svg>We've<br>Reputaion For Excellence</div>
      <div class="value-card"><svg><use href="#i-hands"/></svg>We<br>Build Partnerships</div>
      <div class="value-card featured"><svg><use href="#i-thumb"/></svg>Guided<br>By Commitment</div>
      <div class="value-card"><svg><use href="#i-team"/></svg>A Team<br>Of Professionals</div>
    </div>
  </section>

  <section class="m-services">
    <h2 class="sec-title">OUR SERVICES</h2>
    <div class="photo fire-photo" role="img" aria-label="Home with fire damaged roof"></div>
    <h4>Fire Damage</h4>
    <p>If you use this site regularly and would like to help keep the site...</p>
    <div class="pager"><i><svg><use href="#i-left"/></svg></i><i><svg><use href="#i-right"/></svg></i></div>
  </section>

  <section class="m-other">
    <h2 class="sec-title">OTHER SERVICES</h2>
    <div class="photo kitchen2-photo" role="img" aria-label="Modern gray kitchen"></div>
    <div class="body">
      <h4>Kitchen</h4>
      <p>Fresh layouts, new counters and cabinets fitted to the way your family cooks.</p>
      <span class="read-more">READ MORE</span>
    </div>
    <div class="pager"><i><svg><use href="#i-left"/></svg></i><i><svg><use href="#i-right"/></svg></i></div>
  </section>

  <section class="m-whatwedo">
    <h2 class="sec-title">WHAT WE DO</h2>
    <div class="m-wwd">
      <div class="wwd-item"><div class="wwd-ico"><svg><use href="#i-house"/></svg></div>Home Construction</div>
      <div class="wwd-item"><div class="wwd-ico"><svg><use href="#i-build"/></svg></div>Building Remodeling</div>
      <div class="wwd-item"><div class="wwd-ico"><svg><use href="#i-layout"/></svg></div>Interior Design</div>
      <div class="wwd-item"><div class="wwd-ico"><svg><use href="#i-brick"/></svg></div>Exterior Design</div>
      <div class="wwd-item"><div class="wwd-ico"><svg><use href="#i-reno"/></svg></div>Renovation</div>
      <div class="wwd-item"><div class="wwd-ico"><svg><use href="#i-shield"/></svg></div>Safety Management</div>
    </div>
  </section>

  <section class="m-recent">
    <h2 class="sec-title">RECENT WORK</h2>
    <svg class="arrow" style="left:6px" viewBox="0 0 10 10"><use href="#i-left"/></svg>
    <div class="photo room1" role="img" aria-label="Finished living room"></div>
    <svg class="arrow" style="right:6px" viewBox="0 0 10 10"><use href="#i-right"/></svg>
  </section>

  <section class="m-stats">
    <div class="stat"><b>53</b><span>TOTAL PROJECTS</span></div>
    <div class="stat"><b>371</b><span>STAFF MEMBERS</span></div>
    <div class="stat"><b>15</b><span>WORKING IN STATES</span></div>
    <div class="stat"><b>2,600</b><span>HOURS FOR WORK</span></div>
  </section>

  <section class="m-clients">
    <h2 class="sec-title">OUR CLIENTS</h2>
    <div class="testimonial">
      <p class="tiny">"And for all the wonderful work you and your crew are doing. Our team has nothing but good things to say – we are really fortunate to have found you for this project!"</p>
      <div class="who"><span class="avatar" role="img" aria-label="Client portrait"></span><div><b>John Doe</b><small>Chairman</small></div></div>
    </div>
    <div class="pager"><i><svg><use href="#i-left"/></svg></i><i><svg><use href="#i-right"/></svg></i></div>
  </section>

  <footer class="m-footer">
    <h5>Company</h5>
    <p>We work 7 days a week, every day excluding major holidays. contact us if you have an emergency, with our hotline and contact form.</p>
    <hr>
    <p>Monday – friday: 10:00 – 16:00<br>Saturday: 12:00 – 15:00<br>Sunday and holidays: 09:00 – 12:00</p>
    <h5>Quick Links</h5>
    <ul><li>Home</li><li>About Us</li><li>Services</li><li>Projects / Portfolio</li><li>Contact Us</li></ul>
    <h5>What We Do</h5>
    <ul><li>Home Construction</li><li>Building Remodeling</li><li>Interior Design</li><li>Exterior Design</li><li>Renovation</li><li>Safety Management</li></ul>
    <h5>Contact Us</h5>
    <ul class="ci">
      <li><svg><use href="#i-pin"/></svg>418 W Harbor Crest Ave Tustin, CA 92780</li>
      <li><svg><use href="#i-phone"/></svg>+1 555 014 2287</li>
      <li><svg><use href="#i-mail"/></svg>office@summitbuildersca.example</li>
    </ul>
    <h5>Follow Us</h5>
    <ul class="soc"><li><span class="dot"></span>Friendbook</li><li><span class="dot"></span>Chirper</li><li><span class="dot"></span>WorkLink</li><li><span class="dot"></span>ViewTube</li></ul>
    <div class="foot-brand"><div class="brand"><span class="mark"></span>SUMMIT BUILDERS</div></div>
    <p class="copyright">COPYRIGHT © 2020 <em>SUMMIT BUILDERS</em>. ALL RIGHTS RESERVED.</p>
  </footer>
</main>

</body>
</html>
```